New Business card design to reflect rebrand

I would like a business card design with a good base colour for our new logo and also a placeholder for a profile pic of the card holder. the design needs to be editable to the point that we can easily change the picture of the person and use that design for printmerlo etc. we are looking at a metalic finish business card so will need a good base colour to bring out the finish.

Target Market(s)

prospective customers

Industry/Entity Type

Business

Contact Information for Business Card

I would like one editable design that we can change the name of the card holder and profile picture. The design need to be in a format that be send to printmerlo etc.

Our address is Fenwick Lodge, Copse Lane, Ashby Moor, GU14 3TP Tel no. 01483 556172

Requirements
Must have
• place holder for a profile pic for the card holder. in AI or preferably PSD format

```html
<!DOCTYPE html>
<html lang="en">
<head>
<meta charset="utf-8">
<title>Corval Workplace Services – Business Card</title>
<link rel="stylesheet" href="https://fonts.googleapis.com/css2?family=Open+Sans:wght@400;600;700&display=swap">
<style>
  :root {
    --backdrop: #e9e7e3;
    --orange: #ee6a12;
    --orange-deep: #d9580a;
    --orange-light: #f58a3a;
    --slate: #4d5d78;
    --slate-dark: #3e4c64;
    --text-grey: #6b6b6b;
    --photo-light: #c9c9c9;
    --photo-dark: #9a9a9a;
    --card-white: #ffffff;
    --card-fade: #eeeeee;
  }
  * { box-sizing: border-box; margin: 0; padding: 0; }
  html, body {
    width: 1200px; height: 843px; overflow: hidden;
    background: var(--backdrop);
    font-family: "Open Sans", Arial, sans-serif;
  }
  .canvas {
    position: relative; width: 1200px; height: 843px;
    display: flex; align-items: center; justify-content: center; gap: 40px;
  }
  .card {
    position: relative; width: 540px; height: 309px; overflow: hidden;
    box-shadow: 0 6px 18px rgba(0,0,0,.18);
  }

  /* Back side */
  .card-back {
    background: linear-gradient(160deg, var(--orange-light) 0%, var(--orange) 45%, var(--orange-deep) 100%);
    color: var(--card-white);
    display: flex; flex-direction: column; align-items: center; justify-content: center;
  }
  .card-back .brand-name {
    font-weight: 700; font-size: 40px; letter-spacing: 1px;
    display: flex; align-items: center; gap: 14px;
  }
  .card-back .brand-dot {
    width: 18px; height: 18px; border-radius: 50%; background: var(--card-white);
  }
  .card-back .website {
    margin-top: 30px; font-size: 13px; letter-spacing: 6px;
  }

  /* Front side */
  .card-front {
    background: linear-gradient(180deg, var(--card-white) 0%, var(--card-white) 55%, var(--card-fade) 100%);
  }
  .card-front .shapes { position: absolute; inset: 0; }
  .brand-block {
    position: absolute; left: 44px; top: 30px; width: 260px;
    display: flex; align-items: flex-start; gap: 10px;
  }
  .brand-block .brand-square { flex: none; width: 14px; height: 14px; margin-top: 6px; background: var(--orange); }
  .brand-block .brand-name {
    font-weight: 700; font-size: 22px; line-height: 1.15; color: var(--slate);
  }
  .address {
    position: absolute; left: 44px; top: 130px;
    font-size: 14px; line-height: 20px; color: var(--text-grey); font-style: normal;
  }
  .phone {
    position: absolute; left: 44px; top: 202px;
    font-size: 14px; color: var(--text-grey);
    display: flex; align-items: center; gap: 8px;
  }
  .holder {
    position: absolute; right: 22px; bottom: 14px;
    font-size: 17px; color: var(--card-white); font-weight: 600;
  }
  .holder .role { color: var(--orange); font-weight: 400; font-size: 15px; }
</style>
</head>
<body>
<main class="canvas">

  <section class="card card-back" aria-label="Business card back">
    <div class="brand-name"><span class="brand-dot"></span>Corval</div>
    <div class="website">www.corvalws.com</div>
  </section>

  <section class="card card-front" aria-label="Business card front">
    <svg class="shapes" width="540" height="309" viewBox="0 0 540 309">
      <defs>
        <linearGradient id="profile-fill" x1="0" y1="0" x2="0" y2="1">
          <stop offset="0" stop-color="#c9c9c9"/>
          <stop offset="1" stop-color="#9a9a9a"/>
        </linearGradient>
        <linearGradient id="ribbon-fill" x1="0" y1="0" x2="1" y2="0">
          <stop offset="0" stop-color="#5a6a84"/>
          <stop offset="1" stop-color="#3e4c64"/>
        </linearGradient>
      </defs>
      <rect x="330" y="50" width="190" height="212" fill="url(#profile-fill)" role="img" aria-label="Profile photo of the card holder"/>
      <polygon points="0,248 300,248 296,258 0,258" fill="#ee6a12"/>
      <polygon points="300,248 540,220 540,309 260,309" fill="url(#ribbon-fill)"/>
    </svg>

    <div class="brand-block">
      <span class="brand-square"></span>
      <div class="brand-name">Corval Workplace Services</div>
    </div>

    <address class="address">
      Fenwick Lodge<br>
      Copse Lane, Ashby Moor<br>
      GU14 3TP
    </address>

    <div class="phone">
      <svg width="12" height="14" viewBox="0 0 12 14" aria-hidden="true">
        <path d="M3 1 L5 4 L3.6 5.6 C4.4 7.6 5.6 9 7.4 10 L9 8.6 L11.5 10.8 L10 13 C5 12.6 1.2 8 1 3 Z" fill="#ee6a12"/>
      </svg>
      01483 556172
    </div>

    <div class="holder">Alex Morgan - <span class="role">CEO/Founder</span></div>
  </section>

</main>
</body>
</html>
```